Research and Innovation programme/projects in WOOD based industries

1.Pramenova s.r.o. (offical registered brand name of our company)
-Managing technology development projects
-International cooperation and development European projects
Our company was founded in 2008 and started to work as a counsilary company operating in the section of european funds administrated by Czech republic. Nowadays we are specializing on projects in the sphere of science and research co-financed by EU.Since 6.6.2013 we are registered under European comission for a purpose of broad support of transnational projects.

Target Market(s)

We are primarily focused on european companies, which stand behind the latest research and innovation of sawing, planing, glulam and logging technologies based on wooden materials.

Coding

Coded - Design and coding required

Number of Pages Required

5+ page

Font styles to use
Serif

Colors
cadf82
abd037
9bcb3c
fee18a
ffcf3e
ffc214

Requirements
Must have
• The web will exist in three possible languages in czech, english and deutsch.
• First page : introduction of a company
• Second page : Area of expertise
• Third page: servicies our company provides
• Fourth page: Our partners
• Fifth page: Conditions of our servicies
• Sixth page: Succesful projects
• - we would also love if we had possibility to add videos about our successful projects
• Seventh: Our team
• We are serious company in the sphere of funds and counsilary servicies, that is why we would love to have web design as representative as possible
• Take on mind that that we are specializing on development management, try to apply that on your design
• In the section of contacts, we would love to have photos of our team,
• This is our current site: http://www.pramenova-example.eu/cz/partneri.html
• This is how our concurency sites are lookin. Take these designs as an slight inspiration.
• http://www.lumatrava-example.sk/en/
• https://www2.brenvick-example.com/global/en.html
Nice to have
• Visible logo on the front page for the visitor.
• As a inspiration we provided link for our current web design, but we dont want to copy the current style, just look at the logo and the pages that exists on current web.
• !!!!!!We also uploaded file, where we explain how our cooperation with partner works. Especially in the part 2. section of service. Take that as an ispiration too, or use that to understand, what our company do.
Should not have
• We are serious company in the sphere of funds and counsilary servicies, that is why we would love to have web design representative as possible

```html
<!DOCTYPE html>
<html lang="en">
<head>
<meta charset="utf-8">
<title>Pramenova s.r.o. – Beratungsfirma</title>
<link href="https://fonts.googleapis.com/css2?family=Montserrat:wght@700;800&family=Roboto:wght@400;500;700&display=swap" rel="stylesheet">
<style>
:root{
  --green:#1e9a48;
  --green-dark:#17833c;
  --olive:#6fa228;
  --gold:#e3a51a;
  --amber:#ffc214;
  --ink:#111;
  --text:#555;
  --ghost:#ececec;
  --footer:#1b1b1b;
}
*{box-sizing:border-box;margin:0;padding:0}
html,body{width:1200px;height:4038px;overflow:hidden}
body{position:relative;background:#fff;font-family:"Roboto",sans-serif;color:var(--text)}
.abs{position:absolute}
.head-font{font-family:"Montserrat",sans-serif}

/* header */
.site-header{left:0;top:0;width:1200px;height:52px;background:var(--green)}
.brand{left:110px;top:4px;display:flex;align-items:center;gap:10px}
.brand-square{width:44px;height:40px;background:var(--amber)}
.brand-name{color:var(--amber);font-size:13px;font-weight:700;line-height:18px}
.main-nav{left:381px;top:17px;display:flex;gap:14px;font-size:13px;font-weight:700;color:#fff}
.main-nav .active{color:var(--amber)}
.lang{left:1001px;top:15px;color:#fff;font-size:14px;font-weight:700;display:flex;align-items:center;gap:8px}
.lang .caret{width:0;height:0;border-left:5px solid transparent;border-right:5px solid transparent;border-top:6px solid #fff}
.lang .flag{width:28px;height:16px;background:#c9d0e0}

/* hero */
.hero{left:0;top:52px;width:1200px;height:540px;background:linear-gradient(160deg,#7b8894 0%,#8d857a 45%,#6c5f52 100%)}
.hero-title{left:0;top:205px;width:1200px;text-align:center;color:#fff;font-size:56px;font-weight:800;letter-spacing:1px}
.hero-sub{left:0;top:290px;width:1200px;text-align:center;color:#fff;font-size:15px;font-weight:700}
.hero-curve{left:0;top:0;width:1200px;height:600px}

/* buttons */
.btn{display:inline-flex;align-items:center;justify-content:center;gap:8px;width:186px;height:46px;border-radius:23px;background:var(--green);color:#fff;font-weight:700;font-size:18px}
.btn svg{width:16px;height:16px}

/* section headings */
.ghost{width:1200px;left:0;text-align:center;font-family:"Montserrat",sans-serif;font-weight:800;font-size:64px;color:var(--ghost);white-space:nowrap}
.title{width:1200px;left:0;text-align:center;font-family:"Montserrat",sans-serif;font-weight:800;font-size:44px;color:var(--ink);white-space:nowrap}
.lead{font-size:15px;line-height:26px;color:var(--text);text-align:center}

/* expertise */
.vertical-ghost{left:1110px;top:790px;width:62px;height:650px;writing-mode:vertical-rl;font-family:"Montserrat",sans-serif;font-weight:800;font-size:60px;color:var(--ghost);white-space:nowrap;line-height:62px}
.expertise-photo{left:113px;top:982px;width:467px;height:425px;background:linear-gradient(135deg,#6f7a72,#c9b792 60%,#e6d3a8)}
.expertise-title{left:653px;top:1046px;font-family:"Montserrat",sans-serif;font-weight:700;font-size:41px;color:var(--ink)}
.expertise-text{left:653px;top:1132px;width:432px;font-size:15px;line-height:26px;text-align:justify}

/* services */
.service-card{top:1578px;width:302px;height:380px;border:1px solid #e3e3e3;background:#fff;text-align:center}
.service-card.raised{box-shadow:0 2px 10px rgba(0,0,0,.3);border-color:#ccc}
.service-icon{position:absolute;left:98px;top:18px;width:106px;height:106px;border-radius:50%;background:var(--green)}
.service-name{position:absolute;left:0;top:146px;width:100%;font-size:19px;font-weight:700;color:var(--ink)}
.service-text{position:absolute;left:24px;top:183px;width:254px;font-size:15px;line-height:26px;color:#444}
.service-card .btn{position:absolute;left:58px;top:307px}
.arrow{width:22px;height:30px}

/* partners */
.partners{left:0;top:2000px;width:1200px;height:550px}
.partner-badge{top:2216px;width:199px;height:199px;border-radius:50%;background:rgba(255,255,255,.22)}
.partners .title{color:#fff}

/* projects */
.rule{left:113px;top:2862px;width:974px;height:1px;background:#d8d8d8}
.project-photo{background:linear-gradient(135deg,#8a9188,#4e534c)}
.project-card{top:3153px;width:258px;height:266px;background:#fff;border:1px solid #ddd;text-align:center}
.project-card h3{position:absolute;left:0;top:28px;width:100%;font-size:19px;font-weight:700;color:var(--ink)}
.project-card p{position:absolute;left:30px;top:68px;width:198px;font-size:14px;line-height:26px;color:#666}
.project-card .btn{position:absolute;left:36px;top:194px}
.play{width:52px;height:36px}

/* team */
.team-band{left:0;top:3500px;width:1200px;height:360px}
.team-photo{width:133px;height:133px;border-radius:50%;background:linear-gradient(135deg,#b9b1a8,#6e665f);border:3px solid #fff}
.team-info{font-size:14px;line-height:25.5px;color:#f3f6e6;text-transform:uppercase}
.team-band-title{top:3550px}

/* footer */
.foot-brand{left:110px;top:3918px;display:flex;align-items:center;gap:28px}
.foot-square{width:86px;height:60px;background:var(--amber)}
.foot-name{color:var(--amber);font-size:22px;line-height:32px;font-weight:500}
.foot-nav{left:512px;top:3918px;display:flex;gap:14px;color:#fff;font-size:14px;font-weight:700}
.foot-mail{left:928px;top:3914px;color:#fff;font-size:16px;font-weight:700;display:flex;gap:8px;align-items:center}
.foot-copy{left:512px;top:3964px;color:#fff;font-size:12px;font-weight:700}
.social{left:970px;top:3962px;display:flex;gap:14px}
.social span{width:18px;height:18px;border-radius:50%;background:#fff;display:block}
</style>
</head>
<body>

<header class="site-header abs">
  <div class="brand abs"><span class="brand-square"></span><div class="brand-name">1. PRAMENOVÁ S.R.O.<br>BERATUNGSFIRMA</div></div>
  <nav class="main-nav abs"><span class="active">HOME</span><span>ABOUT US</span><span>OUR SERVICES</span><span>OUR TEAM</span><span>CONTACT</span><span>BLOG</span><span>PROJECTS</span></nav>
  <div class="lang abs">ENG <span class="caret"></span><span class="flag"></span></div>
</header>

<section class="hero abs" role="img" aria-label="Woodworking workshop with a mitre saw on a workbench"></section>
<svg class="hero-curve abs" viewBox="0 0 1200 600" aria-hidden="true">
  <path d="M0 465 Q600 635 1200 460 L1200 600 L0 600Z" fill="#1e9a48"/>
  <path d="M0 468 Q600 712 1200 462 L1200 600 L0 600Z" fill="#fff"/>
</svg>
<h1 class="hero-title abs head-font">PRAMENOVA S.R.O.</h1>
<p class="hero-sub abs">Et harum quidem rerum facilis est et expedita distinctio. Nam libero tempore, Nam libero tempore.</p>
<a class="btn abs" style="left:507px;top:340px">READ MORE <svg viewBox="0 0 16 16"><circle cx="8" cy="8" r="8" fill="#fff"/><path d="M6 4l4 4-4 4" stroke="#1e9a48" stroke-width="2.4" fill="none"/></svg></a>

<!-- welcome -->
<div class="ghost abs" style="top:648px">WELCOME TO PRAMENOVA</div>
<h2 class="title abs" style="top:660px">WELCOME TO PRAMENOVA</h2>
<p class="lead abs" style="left:300px;top:738px;width:600px">Lorem ipsum dolor sit amet, consectetur adipiscing elit, sed do eiusmod tempor incididunt ut labore et dolore magna aliqua. Ut enim ad minim veniam, quis nostrud exercitation ullamco laboris nisi ut aliquip ex ea commodo consequat.</p>
<a class="btn abs" style="left:487px;top:843px">READ MORE <svg viewBox="0 0 16 16"><circle cx="8" cy="8" r="8" fill="#fff"/><path d="M6 4l4 4-4 4" stroke="#1e9a48" stroke-width="2.4" fill="none"/></svg></a>

<!-- expertise -->
<div class="vertical-ghost abs">AREA OF EXPERTISE</div>
<div class="expertise-photo abs" role="img" aria-label="Worker guiding a wooden panel through a CNC machine"></div>
<h2 class="expertise-title abs">AREA OF EXPERTISE</h2>
<p class="expertise-text abs">we denounce with righteous indignation and dislike men who are so beguiled and demoralized by the charms of pleasure of the moment, so blinded by desire, that they cannot foresee the pain and trouble that are bound to ensue; and equal blame belongs to those who fail in their duty.</p>
<a class="btn abs" style="left:653px;top:1288px">READ MORE <svg viewBox="0 0 16 16"><circle cx="8" cy="8" r="8" fill="#fff"/><path d="M6 4l4 4-4 4" stroke="#1e9a48" stroke-width="2.4" fill="none"/></svg></a>

<!-- services -->
<div class="ghost abs" style="top:1478px">OUR SERVICES</div>
<h2 class="title abs" style="top:1490px">OUR SERVICES</h2>
<svg class="arrow abs" style="left:72px;top:1753px" viewBox="0 0 22 30"><path d="M15 5L6 15l9 10" stroke="#222" stroke-width="3" fill="none"/></svg>
<svg class="arrow abs" style="left:1106px;top:1753px" viewBox="0 0 22 30"><path d="M7 5l9 10-9 10" stroke="#222" stroke-width="3" fill="none"/></svg>

<article class="service-card abs" style="left:113px">
  <div class="service-icon"><svg viewBox="0 0 106 106" width="106" height="106"><rect x="32" y="40" width="42" height="30" fill="none" stroke="#fff" stroke-width="4"/><path d="M32 70l42-30M32 40l42 30" stroke="#fff" stroke-width="3"/><rect x="28" y="34" width="50" height="6" fill="#fff"/></svg></div>
  <div class="service-name">PROJECT COORDINATION</div>
  <p class="service-text">Temporibus autem quibusdam et aut officiis debitis aut rerum necessitatibus saepe eveniet ut et voluptates repudiandae.</p>
  <a class="btn">READ MORE <svg viewBox="0 0 16 16"><circle cx="8" cy="8" r="8" fill="#fff"/><path d="M6 4l4 4-4 4" stroke="#1e9a48" stroke-width="2.4" fill="none"/></svg></a>
</article>
<article class="service-card raised abs" style="left:449px">
  <div class="service-icon"><svg viewBox="0 0 106 106" width="106" height="106"><rect x="24" y="44" width="44" height="12" rx="6" fill="#fff"/><rect x="24" y="58" width="44" height="12" rx="6" fill="#fff"/><circle cx="70" cy="50" r="8" fill="#fff"/><circle cx="80" cy="64" r="8" fill="#fff"/></svg></div>
  <div class="service-name">PROJECT FINANCING</div>
  <p class="service-text">At vero eos et accusamus et iusto odio dignissimos ducimus qui blanditiis praesentium voluptatum deleniti atque corrupti quos.</p>
  <a class="btn">READ MORE <svg viewBox="0 0 16 16"><circle cx="8" cy="8" r="8" fill="#fff"/><path d="M6 4l4 4-4 4" stroke="#1e9a48" stroke-width="2.4" fill="none"/></svg></a>
</article>
<article class="service-card abs" style="left:785px">
  <div class="service-icon"><svg viewBox="0 0 106 106" width="106" height="106"><path d="M24 74V50l12 8v-8l12 8v-8l12 8V30h10v44z" fill="#fff"/></svg></div>
  <div class="service-name">EU PROJECTS</div>
  <p class="service-text">On the other hand, we denounce with righteous indignation and dislike men who are so beguiled and demoralized by the charms.</p>
  <a class="btn">READ MORE <svg viewBox="0 0 16 16"><circle cx="8" cy="8" r="8" fill="#fff"/><path d="M6 4l4 4-4 4" stroke="#1e9a48" stroke-width="2.4" fill="none"/></svg></a>
</article>

<!-- partners -->
<svg class="partners abs" viewBox="0 0 1200 550" aria-hidden="true">
  <defs><linearGradient id="partnerFill" x1="0" y1="0" x2="1" y2="0.3"><stop offset="0" stop-color="#1e9a48"/><stop offset="0.55" stop-color="#8fa82a"/><stop offset="1" stop-color="#e3a51a"/></linearGradient></defs>
  <path d="M0 40 Q600 140 1200 10 L1200 530 Q600 420 0 540Z" fill="url(#partnerFill)"/>
</svg>
<div class="partners">
  <div class="ghost abs" style="top:2124px;color:rgba(255,255,255,.18)">OUR PARTNERS</div>
  <h2 class="title abs" style="top:2136px;color:#fff">OUR PARTNERS</h2>
</div>
<div class="partner-badge abs" style="left:111px" role="img" aria-label="Partner badge"></div>
<div class="partner-badge abs" style="left:371px" role="img" aria-label="Partner badge"></div>
<div class="partner-badge abs" style="left:631px" role="img" aria-label="Partner badge"></div>
<div class="partner-badge abs" style="left:890px" role="img" aria-label="Partner badge"></div>

<!-- conditions -->
<div class="ghost abs" style="top:2554px">CONDITIONS OF OUR SERVICES</div>
<h2 class="title abs" style="top:2566px">CONDITIONS OF OUR SERVICES</h2>
<p class="lead abs" style="left:222px;top:2645px;width:756px;color:#333">Et harum quidem rerum facilis est et expedita distinctio. Nam libero tempore, cum soluta nobis est eligendi optio cumque nihil impedit quo minus id quod maxime placeat facere possimus, omnis voluptas assumenda est, omnis dolor repellendus. Et harum quidem rerum facilis est et expedita distinctio. Nam libero tempore. , cum soluta nobis est eligendi optio cumque nihil impedit quo minus id quod .</p>
<a class="btn abs" style="left:507px;top:2775px">READ MORE <svg viewBox="0 0 16 16"><circle cx="8" cy="8" r="8" fill="#fff"/><path d="M6 4l4 4-4 4" stroke="#1e9a48" stroke-width="2.4" fill="none"/></svg></a>
<div class="rule abs"></div>

<!-- projects -->
<div class="ghost abs" style="top:2904px">SUCCESSFUL PROJECTS</div>
<h2 class="title abs" style="top:2916px">SUCCESSFUL PROJECTS</h2>
<svg class="arrow abs" style="left:72px;top:3158px" viewBox="0 0 22 30"><path d="M15 5L6 15l9 10" stroke="#222" stroke-width="3" fill="none"/></svg>
<svg class="arrow abs" style="left:1106px;top:3158px" viewBox="0 0 22 30"><path d="M7 5l9 10-9 10" stroke="#222" stroke-width="3" fill="none"/></svg>

<div class="project-photo abs" style="left:113px;top:3002px;width:282px;height:300px" role="img" aria-label="Forestry tractor parked beside a building"></div>
<svg class="play abs" style="left:226px;top:3133px" viewBox="0 0 52 36"><rect width="52" height="36" rx="10" fill="#222"/><path d="M21 10l12 8-12 8z" fill="#fff"/></svg>
<article class="project-card abs" style="left:309px">
  <h3>SAPIENTE DELECTUS</h3>
  <p>Those who fail in their duty through weakness of will, which is the same as saying through shrinking.</p>
  <a class="btn">READ MORE <svg viewBox="0 0 16 16"><circle cx="8" cy="8" r="8" fill="#fff"/><path d="M6 4l4 4-4 4" stroke="#1e9a48" stroke-width="2.4" fill="none"/></svg></a>
</article>

<div class="project-photo abs" style="left:539px;top:2996px;width:472px;height:313px;background:linear-gradient(120deg,#e98a3a 0%,#c7c9c6 45%,#eef0f0 100%)" role="img" aria-label="Operator working at an industrial machine control panel"></div>
<svg class="play abs" style="left:748px;top:3133px" viewBox="0 0 52 36"><rect width="52" height="36" rx="10" fill="#222"/><path d="M21 10l12 8-12 8z" fill="#fff"/></svg>
<article class="project-card abs" style="left:830px">
  <h3>MAIORES ALIAS</h3>
  <p>we denounce with righteous indignation and dislike men who are so beguiled and demoralized by charms .</p>
  <a class="btn">READ MORE <svg viewBox="0 0 16 16"><circle cx="8" cy="8" r="8" fill="#fff"/><path d="M6 4l4 4-4 4" stroke="#1e9a48" stroke-width="2.4" fill="none"/></svg></a>
</article>

<!-- team + footer background -->
<svg class="abs" style="left:0;top:3500px" width="1200" height="538" viewBox="0 0 1200 538" aria-hidden="true">
  <defs><linearGradient id="teamFill" x1="0" y1="0" x2="1" y2="0"><stop offset="0" stop-color="#5f9d2a"/><stop offset="1" stop-color="#7aa52a"/></linearGradient></defs>
  <rect x="0" y="0" width="1200" height="380" fill="url(#teamFill)"/>
  <path d="M0 355 Q600 270 1200 355 L1200 538 L0 538Z" fill="#1b1b1b"/>
</svg>
<div class="ghost abs" style="top:3540px;color:rgba(255,255,255,.15)">OUR TEAM</div>
<h2 class="title abs" style="top:3552px;color:#fff">OUR TEAM</h2>

<div class="team-photo abs" style="left:124px;top:3628px" role="img" aria-label="Portrait of the managing director"></div>
<div class="team-info abs" style="left:280px;top:3628px">Geschaftsfuhrer<br>T: +420 601 218 445<br>F: +420 601 218 446<br>E-mail: novak@pramenova-example.eu<br>Die Sprache Ihrer Wahl ist English</div>
<div class="team-photo abs" style="left:633px;top:3628px" role="img" aria-label="Portrait of the project manager"></div>
<div class="team-info abs" style="left:790px;top:3640px">Project Manager<br>T: +420 601 218 447<br>Email: dvorakova@pramenova-example.eu<br>Die Sprache Ihrer Wahl ist English</div>

<!-- footer -->
<footer>
  <div class="foot-brand abs"><span class="foot-square"></span><div class="foot-name">1. PRAMENOVÁ S.R.O.<br>BERATUNGSFIRMA</div></div>
  <nav class="foot-nav abs"><span>HOME</span><span>ABOUT US</span><span>OUR SERVICES</span><span>OUR TEAM</span><span>CONTACT</span></nav>
  <div class="foot-mail abs"><svg width="16" height="12" viewBox="0 0 16 12"><rect x="1" y="1" width="14" height="10" fill="none" stroke="#e3a51a" stroke-width="1.5"/><path d="M1 1l7 6 7-6" fill="none" stroke="#e3a51a" stroke-width="1.5"/></svg>info@pramenova-example.eu</div>
  <p class="foot-copy abs">© 2019 Pramenova . All Rights Reserved</p>
  <div class="social abs"><span></span><span></span><span></span><span></span></div>
</footer>

</body>
</html>
```